Accountability Project Graphics

I want to create 10 social media graphics (new Instagram size 4:5 (1080 x 1350 pixels) focusing on our Quilvo Accountability App, using any of the 3 pictures attached. Use the attached pics only, NO RANDOM STOCK PHOTOGRAPHY. For the color scheme, use the landing page colors/fonts (attached).
You can add any of the 3 photos attached but I mainly need BOLD text that includes these headlines and sub-headlines on them.
Please NOTE for all the headlines below, also add this sub-headline on each graphic:
Stay Consistent with RT in Your Pocket!
Here are the headlines:
• Stop Starting Over Every Monday
• You don't need more willpower. You need more support
• Built for women who are tired of doing this alone
• When Motivation Fades, RT Checks In
• The Support System You've Been Missing
• Support When Motivation Disappears
• What if RT Checked in Every Day?
• The Missing Piece Isn't Another Diet
• Eat the food you love. Stay accountable every day.
• One Bad Meal Doesn't Mean You Failed
women over 40 trying to lose weight

```html
<!DOCTYPE html>
<html lang="en">
<head>
<meta charset="utf-8">
<title>Quilvo Accountability – Social Graphics</title>
<link rel="stylesheet" href="https://fonts.googleapis.com/css2?family=Roboto+Slab:wght@700;800&family=Roboto:wght@500&display=swap">
<style>
:root{
  --sheet:#8e8d8f;
  --ink:#2a1a33;
  --hot-pink:#e8467e;
  --mauve:#c4578a;
  --band-pink:#cd5a82;
  --plum:#2f1d45;
  --plum-box:rgba(74,42,85,.92);
  --pink-box:rgba(198,83,131,.92);
  --blush:#fde3ee;
  --blush-light:#fff6fa;
  --white:#ffffff;
}
*{margin:0;padding:0;box-sizing:border-box}
html,body{width:1200px;height:2957px;overflow:hidden;background:var(--sheet)}
.sheet{position:relative;width:1200px;height:2957px}
.tile{position:absolute;width:431px;height:537px;overflow:hidden;background:var(--white)}
.col-left{left:154px}.col-right{left:615px}
.row-1{top:79px}.row-2{top:650px}.row-3{top:1210px}.row-4{top:1776px}.row-5{top:2340px}

.photo{position:absolute}
.photo-portrait{background:linear-gradient(160deg,#6b5248 0%,#3a2a2c 35%,#1c1a22 70%,#15141a 100%)}
.photo-pose{background:linear-gradient(180deg,#fbd3e6 0%,#f7c5dd 30%,#2a2530 31%,#1d1b22 100%)}
.photo-duo{background:linear-gradient(180deg,#d8cfc5 0%,#b9a99a 35%,#3c4a6c 65%,#33415f 100%)}
.photo-hug{background:linear-gradient(90deg,#4a3a6a 0%,#b8b0c0 30%,#e26aa5 55%,#f6dce8 80%,#fbe9f2 100%)}

.panel-text{position:absolute;top:0;bottom:0;background:linear-gradient(180deg,var(--blush-light),var(--blush))}
.panel-pose{position:absolute;left:0;top:0;width:215px;height:537px;background:linear-gradient(180deg,#fbd3e6,#f9cde2)}

.headline{position:absolute;font-family:"Roboto Slab",Georgia,serif;font-weight:800;color:var(--ink);line-height:1.18}
.headline .pink{color:var(--hot-pink)}
.headline .mauve{color:var(--mauve)}

.band{position:absolute;left:0;width:431px;top:375px;height:82px;display:flex;align-items:center;justify-content:center;text-align:center;font-family:Roboto,Arial,sans-serif;font-weight:500;font-size:23px;line-height:1.3;color:var(--white);padding:0 30px}
.band-pink{background:var(--band-pink)}
.band-plum{background:var(--plum)}
.band-plum .accent{color:var(--hot-pink)}
.band-low{top:387px;height:88px}

.base{position:absolute;left:0;width:431px;top:316px;bottom:0}
.base-plum{background:var(--plum)}
.base-pink{background:var(--band-pink)}
.sub-free{position:absolute;left:0;width:431px;top:432px;text-align:center;font-family:Roboto,Arial,sans-serif;font-weight:500;font-size:26px;line-height:1.3;color:var(--white)}

.callout{position:absolute;top:200px;height:206px;border-radius:16px;display:flex;flex-direction:column;align-items:center;justify-content:center;text-align:center;font-family:"Roboto Slab",Georgia,serif;font-weight:800;color:var(--white);line-height:1.08}
.callout-pink{left:41px;width:348px;background:var(--pink-box);font-size:34px}
.callout-plum{left:25px;width:381px;background:var(--plum-box)}
.callout .big{font-size:68px}
.callout .mid{font-size:32px;margin:4px 0}
.callout .large{font-size:52px}
.callout-food{left:22px;width:387px;font-size:38px;line-height:1.22}
.below-white{position:absolute;left:0;width:431px;top:475px;bottom:0;background:var(--white)}
.below-blush{position:absolute;left:0;width:215px;top:457px;bottom:0;background:#fde0ec}
</style>
</head>
<body>
<main class="sheet">

  <!-- 1 -->
  <section class="tile col-left row-1">
    <div class="panel-text" style="left:0;width:215px"></div>
    <div class="photo photo-portrait" style="left:215px;top:0;width:216px;height:537px" role="img" aria-label="Smiling coach in a black lace top, portrait"></div>
    <h2 class="headline" style="left:25px;top:84px;font-size:37px">Stop<br>Starting<br><span class="mauve" style="font-size:46px;line-height:1.1">Over<br>Every</span><br>Monday</h2>
    <div class="below-blush"></div>
    <p class="band band-pink">Stay Consistent with RT in Your Pocket!</p>
  </section>

  <!-- 2 -->
  <section class="tile col-right row-1">
    <div class="photo photo-duo" style="left:0;top:0;width:431px;height:316px" role="img" aria-label="Coach and client laughing together indoors"></div>
    <div class="base base-plum"></div>
    <h2 class="callout callout-pink">You don't need<br>more willpower.<br>You need<br>more support</h2>
    <p class="sub-free">Stay Consistent with<br>RT in Your Pocket!</p>
  </section>

  <!-- 3 -->
  <section class="tile col-left row-2">
    <div class="panel-text" style="left:215px;width:216px"></div>
    <div class="photo photo-pose panel-pose" role="img" aria-label="Coach in black outfit posing with hand on hip"></div>
    <h2 class="headline" style="left:235px;top:28px;font-size:40px;line-height:48px">Built for<br>women<br><span class="pink">who are<br>tired of<br>doing</span><br>this<br>alone</h2>
    <div class="below-blush" style="left:215px;width:216px"></div>
    <p class="band band-plum band-low" style="top:394px;height:81px">Stay Consistent with<br><span class="accent">RT in Your Pocket!</span></p>
  </section>

  <!-- 4 -->
  <section class="tile col-right row-2">
    <div class="photo photo-hug" style="left:0;top:0;width:431px;height:387px" role="img" aria-label="Coach warmly hugging a client"></div>
    <h2 class="headline" style="left:212px;top:36px;width:210px;text-align:center;font-size:38px;line-height:1.12">When<br>Motivation<br>Fades,<br><span class="pink" style="font-size:48px;line-height:1.02">RT<br>Checks<br>In</span></h2>
    <p class="band band-pink band-low">Stay Consistent with RT in Your Pocket!</p>
    <div class="below-white"></div>
  </section>

  <!-- 5 -->
  <section class="tile col-left row-3">
    <div class="panel-text" style="left:0;width:215px"></div>
    <div class="photo photo-portrait" style="left:215px;top:0;width:216px;height:537px" role="img" aria-label="Smiling coach in a black lace top, portrait"></div>
    <h2 class="headline" style="left:25px;top:56px;font-size:38px;line-height:47px"><span class="pink">The<br>Support<br>System</span><br>You've<br>Been<br>Missing</h2>
    <div class="below-blush"></div>
    <p class="band band-pink">Stay Consistent with<br>RT in Your Pocket!</p>
  </section>

  <!-- 6 -->
  <section class="tile col-right row-3">
    <div class="photo photo-duo" style="left:0;top:0;width:431px;height:316px" role="img" aria-label="Coach and client laughing together indoors"></div>
    <div class="base base-pink"></div>
    <h2 class="callout callout-plum"><span class="big">Support</span><span class="mid">When Motivation</span><span class="large">Disappears</span></h2>
    <p class="sub-free">Stay Consistent with<br>RT in Your Pocket!</p>
  </section>

  <!-- 7 -->
  <section class="tile col-left row-4">
    <div class="panel-text" style="left:215px;width:216px"></div>
    <div class="photo photo-pose panel-pose" role="img" aria-label="Coach in black outfit posing with hand on hip"></div>
    <h2 class="headline" style="left:215px;top:46px;width:216px;text-align:center;font-size:38px;line-height:1.15"><span class="pink" style="font-size:48px;line-height:1">WHAT</span><br><span class="pink" style="font-size:62px;line-height:1">IF</span><br>RT<br>Checked<br>in Every<br>Day?</h2>
    <div class="below-blush" style="left:215px;width:216px"></div>
    <p class="band band-plum" style="top:394px;height:81px">Stay Consistent with<br><span class="accent">RT in Your Pocket!</span></p>
  </section>

  <!-- 8 -->
  <section class="tile col-right row-4">
    <div class="photo photo-hug" style="left:0;top:0;width:431px;height:387px" role="img" aria-label="Coach warmly hugging a client"></div>
    <h2 class="headline" style="left:222px;top:48px;width:206px;text-align:center;font-size:40px;line-height:1.15"><span class="pink">The<br>Missing<br>Piece</span><br>Isn't<br>Another<br><span style="font-size:64px;line-height:.95">Diet</span></h2>
    <p class="band band-pink band-low">Stay Consistent with RT in Your Pocket!</p>
    <div class="below-white"></div>
  </section>

  <!-- 9 -->
  <section class="tile col-left row-5">
    <div class="photo photo-duo" style="left:0;top:0;width:431px;height:316px" role="img" aria-label="Coach and client laughing together indoors"></div>
    <div class="base base-pink"></div>
    <h2 class="callout callout-plum callout-food">Eat the food<br>you love.<br>Stay accountable<br>every day.</h2>
    <p class="sub-free">Stay Consistent with<br>RT in Your Pocket!</p>
  </section>

  <!-- 10 -->
  <section class="tile col-right row-5">
    <div class="panel-text" style="left:0;width:215px"></div>
    <div class="photo photo-portrait" style="left:215px;top:0;width:216px;height:537px" role="img" aria-label="Smiling coach in a black lace top, portrait"></div>
    <h2 class="headline" style="left:31px;top:30px;font-size:40px;line-height:48px">One<br>Bad<br>Meal<br><span class="pink">Doesn't<br>Mean<br>You<br>Failed</span></h2>
    <div class="below-blush"></div>
    <p class="band band-plum">Stay Consistent with<br><span class="accent">RT in Your Pocket!</span></p>
  </section>

</main>
</body>
</html>
```